Book Cover for Lantern Cousins Notes from the Orchard

We have written a book that brings together Notes from the Orchard from a variety of women's voices.
We developed a draft book cover that we like using Canva (attached below). We'd love a book cover that is similar to this image, but looks more professional.
Following are the themes we’d like to depict in the book cover, and in parentheses, how they are represented in the current cover:
1. Divinely feminine (overall cover)
2. Currents of enlightenment (the swirls of light carrying the butterfly)
3. Diversity (a myriad of colors)
4. The solo journey into the unknown (the single butterfly’s flight)
5. Buoyancy and joy (again, the dancing colors and floating butterfly)
6. Boldly feminine (the blue butterfly, set against brush strokes of light)
7. Homage to a dear friend (she loved blue butterflies, the cosmos - this butterfly has hints of the cosmos in her wings, and painting - this background has brush strokes of light).
Book Title, Subtitle, and Editor:
Lantern Cousins
Notes from the Orchard
Edited by Ilse Varno
Thank you very much for considering this project!
People who are interested in Women and Spirituality

```html
<!DOCTYPE html>
<html lang="en">
<head>
<meta charset="utf-8">
<title>Lantern Cousins – Book Cover</title>
<link rel="stylesheet" href="https://fonts.googleapis.com/css2?family=Playfair+Display:wght@600&family=Great+Vibes&family=Lora:ital@1&display=swap">
<style>
  :root {
    --stage: #e6e4e9;
    --paper-light: #ffffff;
    --paper-shade: #ececec;
    --title-purple: #5e1f7e;
    --subtitle-pink: #d4136f;
    --editor-ink: #1c1c1c;
    --wash-lavender: rgba(150, 150, 205, 0.6);
    --wash-pink: rgba(214, 140, 180, 0.6);
    --wash-sky: rgba(170, 205, 235, 0.55);
    --wing-deep: #2f6fd6;
    --wing-blue: #4a90e6;
    --wing-aqua: #45c8e8;
  }
  * { margin: 0; padding: 0; box-sizing: border-box; }
  html, body {
    width: 1200px;
    height: 800px;
    overflow: hidden;
    background: var(--stage);
  }
  .book-cover {
    position: absolute;
    left: 346px;
    top: 20px;
    width: 507px;
    height: 760px;
    background: linear-gradient(90deg, var(--paper-shade) 0%, var(--paper-light) 30%, var(--paper-light) 75%, var(--paper-shade) 100%);
    overflow: hidden;
  }
  .watercolour-wash {
    position: absolute;
    left: 0;
    top: 240px;
    width: 507px;
    height: 460px;
    background:
      radial-gradient(ellipse 150px 130px at 28% 48%, var(--wash-lavender) 0%, rgba(150,150,205,0) 100%),
      radial-gradient(ellipse 170px 140px at 66% 40%, var(--wash-pink) 0%, rgba(214,140,180,0) 100%),
      radial-gradient(ellipse 100px 120px at 92% 45%, var(--wash-sky) 0%, rgba(170,205,235,0) 100%),
      radial-gradient(ellipse 120px 60px at 60% 80%, rgba(214,160,195,0.3) 0%, rgba(214,160,195,0) 100%);
  }
  .butterfly-art {
    position: absolute;
    left: 140px;
    top: 392px;
    width: 215px;
    height: 272px;
    background: linear-gradient(165deg, var(--wing-deep) 0%, var(--wing-blue) 35%, var(--wing-aqua) 70%, var(--wing-blue) 100%);
    border-radius: 62% 38% 48% 52% / 42% 36% 64% 58%;
    transform: rotate(8deg);
    opacity: 0.92;
  }
  .cover-type {
    position: absolute;
    inset: 0;
  }
  .title-line {
    font-family: "Playfair Display", "Times New Roman", serif;
    font-weight: 600;
    fill: var(--title-purple);
  }
  .subtitle {
    font-family: "Great Vibes", cursive;
    fill: var(--subtitle-pink);
  }
  .subtitle-rule {
    stroke: var(--subtitle-pink);
    stroke-width: 1;
  }
  .editor-credit {
    font-family: "Lora", Georgia, serif;
    font-style: italic;
    fill: var(--editor-ink);
  }
</style>
</head>
<body>
  <main class="book-cover">
    <div class="watercolour-wash" role="img" aria-label="Soft watercolour wash in lavender, pink and sky blue"></div>
    <div class="butterfly-art" role="img" aria-label="A single blue watercolour butterfly in flight"></div>
    <svg class="cover-type" width="507" height="760" viewBox="0 0 507 760">
      <text class="title-line" x="58" y="148" font-size="128" textLength="414" lengthAdjust="spacingAndGlyphs">LANTERN</text>
      <text class="title-line" x="68" y="262" font-size="128" textLength="403" lengthAdjust="spacingAndGlyphs">COUSINS</text>
      <line class="subtitle-rule" x1="109" y1="296" x2="398" y2="296"/>
      <text class="subtitle" x="253.5" y="334" font-size="34" text-anchor="middle">Notes from the Orchard</text>
      <line class="subtitle-rule" x1="109" y1="349" x2="398" y2="349"/>
      <text class="editor-credit" x="254" y="733" font-size="23" text-anchor="middle">Edited by Ilse Varno</text>
    </svg>
  </main>
</body>
</html>
```